Business Cards for new orthopaedic surgery practice

My husband and I are starting our own orthopaedic surgery practice. We are looking for a business card that is uniform, but one will have my name/title and the other will have his. You can just create one design with my name on it for now. But when I choose your design as the winning design I will ask that you add another copy with his name/title.

We are looking for classy, simple, elite all in one. We like dark blues/a little gold/yellow. Something that goes with our logo. We want our logo incorporated. Here is all the info you need:
Business name: RV Bone & Vitality Center
Location: 38517 North Willowmere Ave
Palm Harbor Grove, FL 33498
Phone: 954-218-4063
Fax: 954-582-7341
Email: info@myrvbonecare.example

Names: Lydia Vance, M.D.
Board Certified Hand and Upper Extremity Surgeon

Ebo Dansu, M.D.
Board Certified Hip & Knee Replacement/General Orthopaedic Surgeon

Can decide what you want to put on the back. Maybe a slogan:
Rooted in Care. Focused on You

I am just going to upload our logo. The only thing is if we select you as the winning design, the location, and phone numbers may change. We will need your help to update that once fully solidified.

Industry/Entity Type

Medical

Contact Information for Business Card

Colors
0054AA
0677BA
7BADD7
CADEEF
E8F1F8
0094D4
00A9DD
6FCCEA
C7EBF8
E9F6FB

Requirements
Must have
• class, appeal,
Should not have
• We want to air on the side of masculine if we are looking at masculine vs. feminine feel. But we still want it classy, sophisticated, and something we will love

```html
<!DOCTYPE html>
<html lang="en">
<head>
<meta charset="utf-8">
<title>RV Bone &amp; Vitality Center – Business Card</title>
<link rel="stylesheet" href="https://fonts.googleapis.com/css2?family=Cinzel:wght@600&family=Poppins:wght@400;600&display=swap">
<style>
  :root {
    --stage: #1b1c1f;
    --card-blue: #233a86;
    --card-deep: #1e3277;
    --accent-cyan: #2bb6e3;
    --text-white: #ffffff;
  }
  * { box-sizing: border-box; margin: 0; padding: 0; }
  html, body {
    width: 1200px; height: 900px; overflow: hidden;
    background: var(--stage);
  }
  .stage {
    position: relative; width: 1200px; height: 900px;
    display: flex; flex-direction: column; align-items: center; justify-content: center; gap: 32px;
  }
  .card {
    position: relative; width: 620px; height: 354px;
    background: var(--card-blue);
    border-radius: 4px;
    box-shadow: 0 18px 40px rgba(0,0,0,.55);
    overflow: hidden;
    color: var(--text-white);
  }

  /* Shared wordmark */
  .brand {
    position: absolute; left: 0; right: 0;
    font-family: "Cinzel", serif; font-weight: 600; color: var(--text-white);
    text-align: center; line-height: 1.15;
  }
  .brand-line { display: block; }
  .brand-sub {
    display: flex; align-items: center; justify-content: center; gap: 12px;
    margin-top: 4px;
  }
  .brand-sub .rule { width: 70px; height: 1px; background: var(--text-white); }

  /* Front */
  .card-front .brand { top: 54px; font-size: 32px; }
  .card-front .brand-sub { font-size: 24px; }
  .contact-block {
    position: absolute; left: 30px; right: 30px; top: 178px;
    display: flex; align-items: stretch; justify-content: center; gap: 20px;
  }
  .person { text-align: right; font-family: "Poppins", sans-serif; }
  .person-name { font-weight: 600; font-size: 17px; color: var(--accent-cyan); }
  .person-title { font-size: 12.5px; margin-top: 4px; }
  .divider { width: 1px; background: var(--text-white); }
  .contact-list { list-style: none; font-family: "Poppins", sans-serif; font-size: 12.5px; }
  .contact-list li { display: flex; align-items: center; gap: 7px; line-height: 1.75; white-space: nowrap; }
  .contact-icon { width: 12px; height: 12px; fill: var(--text-white); flex: none; }
  .address {
    position: absolute; left: 0; right: 0; bottom: 38px; text-align: center;
    font-family: "Poppins", sans-serif; font-size: 13px;
  }

  /* Back */
  .back-mark {
    position: absolute; left: 50%; top: 50%; width: 300px; height: 300px;
    transform: translate(-50%, -50%);
    border-radius: 50%; background: var(--card-deep);
  }
  .card-back .brand { top: 104px; font-size: 34px; }
  .card-back .brand-sub { font-size: 26px; }
  .tagline {
    position: absolute; left: 0; right: 0; top: 236px; text-align: center;
    font-family: "Poppins", sans-serif; font-size: 15px; color: var(--accent-cyan);
  }
</style>
</head>
<body>
<main class="stage">

  <section class="card card-front" aria-label="Business card front">
    <h1 class="brand">
      <span class="brand-line">RV Bone &amp; Vitality</span>
      <span class="brand-sub"><span class="rule"></span>Center<span class="rule"></span></span>
    </h1>

    <div class="contact-block">
      <div class="person">
        <p class="person-name">Lydia Vance, M.D.</p>
        <p class="person-title">Hand and Upper Extremity Surgery</p>
      </div>
      <div class="divider"></div>
      <ul class="contact-list">
        <li>
          <svg class="contact-icon" viewBox="0 0 24 24" aria-hidden="true"><path d="M6.6 10.8a15 15 0 0 0 6.6 6.6l2.2-2.2c.3-.3.7-.4 1-.2 1.1.4 2.3.6 3.6.6.6 0 1 .4 1 1V20c0 .6-.4 1-1 1A17 17 0 0 1 3 4c0-.6.4-1 1-1h3.5c.6 0 1 .4 1 1 0 1.3.2 2.5.6 3.6.1.3 0 .7-.2 1z"/></svg>
          954-218-4063
        </li>
        <li>
          <svg class="contact-icon" viewBox="0 0 24 24" aria-hidden="true"><path d="M6 2h10v6H6zM4 9h16a2 2 0 0 1 2 2v7h-4v4H6v-4H2v-7a2 2 0 0 1 2-2zm4 8v3h8v-3z"/></svg>
          954-582-7341
        </li>
        <li>
          <svg class="contact-icon" viewBox="0 0 24 24" aria-hidden="true"><path d="M2 5h20v14H2zm2 2v.5l8 5 8-5V7l-8 5z"/></svg>
          info@myrvbonecare.example
        </li>
      </ul>
    </div>

    <p class="address">38517 North Willowmere Ave, Palm Harbor Grove, FL 33498</p>
  </section>

  <section class="card card-back" aria-label="Business card back">
    <div class="back-mark"></div>
    <h2 class="brand">
      <span class="brand-line">RV Bone &amp; Vitality</span>
      <span class="brand-sub"><span class="rule"></span>Center<span class="rule"></span></span>
    </h2>
    <p class="tagline">Steady in Care Centered on You</p>
  </section>

</main>
</body>
</html>
```